Hardcore nerd needs to stand out in a sea of dull Defence business cards

Wombarra Devices is a new Australian consulting engineering company that turns research and theory into practical systems. No evangelistic fluff, just mathematics and physics into electronic and optical circuits for consumer products, scientific research or Defence applications.

We already have a recognised logo (provided) which is often dark blue/black on a light background but we're open to other combinations. (Us engineers tend to have limited aesthetic imagination :)

Some of our recent products have included:
* Instrumentation for electrical testing,
* Radar jammers,
* GPS antenna design,
* Satellite tracking systems,
* High power lasers

We're open to both single and double-sided designs - happy to be convinced either way.

P.S. Another group is working on the web page, so - alas - our web site is currently of no use for images/ideas...

Target Market(s)

Engineering managers,
Scientists

Contact Information for Business Card

Dr Colin Harte
R&D Engineer

colin@wombarradevices.com.au
0427 563 710

PO Box XXX (to be confirmed)
Kelsby ACT 2917
Australia

Font styles to use
Serif
Sans Serif

Colors

Designer to choose colors to be used in the design.

Requirements
Must have
• My contact details!
• I've had many (great) "bold and plain" designs submitted already, so feel free to be artistically creative :)
• Happy to take advice re fonts/colours/printability etc.
Nice to have
• I'm not sure if "lists" are more at home on a CV than a business card, but representative services include:
• Applied electromagnetics
• RF and high speed electronics
• Signal and image processing
• Electro-optical and laser systems
• Concept-to-prototype design services
• If you're considering double sided cards, then often measuring/alignment grids/rulers feature on the back of similar cards.
• e.g. https://www.veltranoptics.example/newgrouppage9.cfm?objectgroup_id=4183
• https://www.veltranoptics.example/newgrouppage9.cfm?objectgroup_ID=4185
• ..or even a "Smith chart" (google will return lots)
• Generic images to represent a capability might work - googling images associated with keyword for each of these areas might help:
• - "passive radar", "phased array", "fdtd", "vircator"
• RF and high speed electronic design
• - "smith chart", "microstrip circuits", "dimensioned drawing", "electronic schematic"
• - "dft", "iir filter"
• - "optical cavity". "laser energy level diagram"
• Background/watermarked images outlines/wireframes/schematics would probably look OK.
Should not have
• If a list of projects/services is provided, it is important not to make the client feel that this is "all" the company can do. Engineering design is a creative discipline (like graphics :)
• Please, no stock "military" snaps like planes, missiles, etc!

```html
<!DOCTYPE html>
<html lang="en">
<head>
<meta charset="utf-8">
<title>Wombarra Devices – Business Card</title>
<link rel="stylesheet" href="https://fonts.googleapis.com/css2?family=Arimo:wght@700&family=Lato:wght@400;700&display=swap">
<style>
  :root {
    --backdrop: #7a4a26;
    --kraft-light: #d9b98e;
    --kraft: #c79d6c;
    --kraft-dark: #b88c5c;
    --ink: #111111;
    --shadow: rgba(0, 0, 0, 0.45);
  }
  * { margin: 0; padding: 0; box-sizing: border-box; }
  html, body {
    width: 1200px;
    height: 900px;
    overflow: hidden;
  }
  body {
    position: relative;
    background: var(--backdrop);
    font-family: "Lato", Arial, sans-serif;
    color: var(--ink);
  }
  .card {
    position: absolute;
    background: radial-gradient(ellipse at 50% 20%, var(--kraft-light) 0%, var(--kraft) 55%, var(--kraft-dark) 100%);
    box-shadow: 2px 4px 8px var(--shadow);
  }
  .card--front { left: 330px; top: 90px; width: 555px; height: 343px; }
  .card--back  { left: 330px; top: 469px; width: 559px; height: 343px; }

  .centered { position: absolute; left: 0; width: 100%; text-align: center; }

  .contact__name {
    top: 66px;
    font-family: "Arimo", Arial, sans-serif;
    font-weight: 700;
    font-size: 21px;
    letter-spacing: 0.3px;
  }
  .contact__role { top: 89px; font-size: 15px; }
  .contact__icons { position: absolute; left: 188px; top: 121px; }
  .contact__details { top: 150px; font-size: 16px; line-height: 20.5px; }
  .contact__rule {
    position: absolute; left: 188px; top: 225px;
    width: 183px; height: 1px; background: var(--ink);
  }
  .contact__address { top: 236px; font-size: 16px; line-height: 20px; }

  .brand { position: absolute; left: 108px; top: 90px; display: flex; align-items: center; gap: 18px; }
  .brand__mark { width: 110px; height: 110px; border-radius: 50%; background: var(--ink); }
  .brand__name {
    font-weight: 700;
    font-size: 38px;
    line-height: 40px;
    letter-spacing: 2px;
    text-transform: uppercase;
  }

  .services {
    position: absolute; left: 41px; top: 268px;
    display: grid; grid-template-columns: 222px auto;
    font-size: 16px; line-height: 20px;
    list-style: none;
  }
  .services li::before { content: "• "; }
</style>
</head>
<body>
  <section class="card card--front" aria-label="Card front">
    <p class="centered contact__name">DR COLIN HARTE</p>
    <p class="centered contact__role">R&amp;D Engineer</p>
    <svg class="contact__icons" width="180" height="24" viewBox="0 0 180 24" aria-hidden="true">
      <line x1="0" y1="12" x2="51" y2="12" stroke="#111" stroke-width="1"/>
      <line x1="127" y1="12" x2="180" y2="12" stroke="#111" stroke-width="1"/>
      <circle cx="63" cy="12" r="11" fill="#111"/>
      <path d="M57 9 q6 -5 12 0 l-2 2 h-2 v-1 h-4 v1 h-2z M58 12 h10 v5 h-10z" fill="#c79d6c"/>
      <circle cx="89" cy="12" r="11" fill="#111"/>
      <rect x="82" y="7" width="14" height="10" fill="none" stroke="#c79d6c" stroke-width="1.5"/>
      <polyline points="82,7 89,13 96,7" fill="none" stroke="#c79d6c" stroke-width="1.5"/>
      <circle cx="115" cy="12" r="11" fill="#111"/>
      <circle cx="115" cy="12" r="6.5" fill="none" stroke="#c79d6c" stroke-width="1.5"/>
      <ellipse cx="115" cy="12" rx="3" ry="6.5" fill="none" stroke="#c79d6c" stroke-width="1"/>
      <line x1="108.5" y1="12" x2="121.5" y2="12" stroke="#c79d6c" stroke-width="1"/>
    </svg>
    <p class="centered contact__details">0427 563 710<br>colin@wombarradevices.com.au<br>www.wombarradevices.com.au</p>
    <div class="contact__rule"></div>
    <p class="centered contact__address">PO Box XXX<br>Kelsby ACT 2917, Australia</p>
  </section>

  <section class="card card--back" aria-label="Card back">
    <div class="brand">
      <div class="brand__mark"></div>
      <p class="brand__name">Wombarra<br>Devices</p>
    </div>
    <ul class="services">
      <li>Applied electromagnetics</li>
      <li>RF and high speed electronics</li>
      <li>Signal and image processing</li>
      <li>Electro-optical and laser systems</li>
    </ul>
  </section>
</body>
</html>
```